Newsletter Ad

I am looking for someone to design an advertisement for a mother's club newsletter. 4" wide X by 5" tall (and 2.5" wide X 5" tall if possible).

I'm a psychotherapist, so want the ad to look professional, but modern. I have a logo with my photo attached that can be incorporated into the design. The colors of my website are turquoise and white. I'd like to keep with that theme...so maybe some turquoise blocking to match the logo font color.

I'm uploading a logo as well as an ad draft with the content I'd like listed in the ad.

```html
<!DOCTYPE html>
<html lang="en">
<head>
<meta charset="utf-8">
<title>Dana Whitlow, MA, MFT – Psychotherapy</title>
<link href="https://fonts.googleapis.com/css2?family=Questrial&display=swap" rel="stylesheet">
<style>
  :root {
    --teal: #3a9a98;
    --teal-dark: #2f8684;
    --grey: #6e6e6e;
    --rule: #8a8a8a;
    --ink: #111111;
    --white: #ffffff;
  }
  html, body {
    margin: 0;
    padding: 0;
    overflow: hidden;
    background: var(--white);
  }
  .ad {
    position: relative;
    width: 961px;
    height: 1200px;
    background: var(--white);
    font-family: "Questrial", "Century Gothic", sans-serif;
    overflow: hidden;
  }
  .portrait {
    position: absolute;
    left: 56px;
    top: 107px;
    width: 146px;
    height: 190px;
    background: linear-gradient(160deg, #2a2420 0%, #8a6a4e 45%, #c9a27c 70%, #3a302a 100%);
  }
  .name {
    position: absolute;
    left: 243px;
    top: 100px;
    margin: 0;
    font-size: 58px;
    font-weight: 400;
    color: var(--teal);
    letter-spacing: 0.5px;
    white-space: nowrap;
  }
  .name-rule {
    position: absolute;
    left: 245px;
    top: 181px;
    width: 558px;
    height: 2px;
    background: var(--rule);
  }
  .service {
    position: absolute;
    left: 0;
    width: 1070px;
    text-align: center;
    top: 198px;
    margin: 0;
    font-size: 60px;
    color: var(--grey);
    white-space: nowrap;
  }
  .service small {
    font-size: 32px;
  }
  .audience {
    position: absolute;
    left: 270px;
    top: 266px;
    margin: 0;
    font-size: 35px;
    color: var(--grey);
    white-space: nowrap;
  }
  .focus-band {
    position: absolute;
    left: 0;
    top: 358px;
    width: 961px;
    height: 574px;
    background: var(--teal);
  }
  .focus-list {
    list-style: none;
    margin: 0;
    padding: 0;
    position: absolute;
    left: 0;
    top: 42px;
    width: 961px;
    text-align: center;
    color: var(--white);
    font-size: 39px;
    line-height: 60.6px;
  }
  .contact {
    position: absolute;
    left: 0;
    top: 938px;
    width: 961px;
    text-align: center;
    color: var(--ink);
    font-size: 35px;
    line-height: 47.5px;
    font-style: normal;
  }
  .contact p { margin: 0; }
  .footer-band {
    position: absolute;
    left: 0;
    top: 1139px;
    width: 961px;
    height: 61px;
    background: var(--teal);
  }
  .license {
    position: absolute;
    right: 25px;
    top: 17px;
    margin: 0;
    color: var(--white);
    font-size: 22px;
  }
</style>
</head>
<body>
  <div class="ad">
    <div class="portrait" role="img" aria-label="Portrait photo of the therapist"></div>
    <h1 class="name">DANA WHITLOW, MA, MFT</h1>
    <div class="name-rule"></div>
    <p class="service">Psychotherapy <small>for</small></p>
    <p class="audience">Individuals, Couples and Families</p>

    <section class="focus-band">
      <ul class="focus-list">
        <li>Parenting</li>
        <li>Depression</li>
        <li>Anxiety</li>
        <li>Life Transitions</li>
        <li>Divorce</li>
        <li>Couples Issues</li>
        <li>Women’s Issues</li>
        <li>Attachment and Neuroscience</li>
      </ul>
    </section>

    <address class="contact">
      <p>418 Alder Street, Bayside, CA 94000</p>
      <p>www.danawhitlow.com</p>
      <p>dana@danawhitlow.com</p>
      <p>415.555.0188</p>
    </address>

    <footer class="footer-band">
      <p class="license">License# MFC20418</p>
    </footer>
  </div>
</body>
</html>
```